Business card

We need a business card design for our company based in Auckland , New Zealand called 'Ridge + Studio Ltd'. We provide architectural services. We would like to see designs that use the max. three colours (such as white, black, grey) The final design should communicate financial safety and growth."
Also I will provide our company logo. I would like to the logo to be embeded onto our business card.

Target Market(s)

new residential house, alteration & addition & light commericila design & drafting service

Industry/Entity Type

Architecture

Contact Information for Business Card

Company name: ridge + studio Ltd.
Name: Mark Delford
Job title: architectural designer & Design RDC
email address: mark@rplusd.co.nz
mobile number: 02 5163 2290
web site: www.rplusd.co.nz

Requirements
Must have
• My project must have..
• - embeded logo (attached company logo)
• I don't have a bigger version for our company logo, but I have one old one, so you can remove the word from it)
• - insert the attached small BKTW logo & LBP logo
• - creative, simple and clear business card.
• - Max. three colours
Nice to have
• - Here are the samples I would like to share with you: http://www.plimvora.com/blog/minimalistic-business-card-designs/
• I would like to have my business card like one of the creation.
Should not have
• TBA

```html
<!DOCTYPE html>
<html lang="en">
<head>
<meta charset="utf-8">
<title>Ridge + Studio Ltd — Business Card</title>
<link rel="stylesheet" href="https://fonts.googleapis.com/css2?family=PT+Sans:wght@400;700&family=PT+Sans+Narrow&display=swap">
<style>
  :root {
    --backdrop: #e4e4e4;
    --card: #ffffff;
    --ink: #111111;
    --text: #333333;
    --grey: #8c9696;
    --rule: #d6d6d6;
    --muted: #777777;
    --badge: #2b2b2b;
    --partner: #555555;
  }
  * { box-sizing: border-box; margin: 0; padding: 0; }
  html, body {
    width: 1105px;
    height: 1200px;
    overflow: hidden;
    background: var(--backdrop);
    font-family: "PT Sans", sans-serif;
  }
  .card {
    position: absolute;
    left: 193px;
    width: 720px;
    height: 410px;
    background: var(--card);
    overflow: hidden;
  }
  .card--front { top: 167px; }
  .card--back { top: 623px; }

  .divider {
    position: absolute;
    left: 336px;
    width: 1px;
    background: var(--rule);
  }

  /* Front */
  .brand {
    position: absolute;
    left: 86px;
    top: 88px;
    width: 220px;
    height: 220px;
    display: flex;
    flex-direction: column;
    align-items: center;
    justify-content: center;
    gap: 16px;
  }
  .brand__dot {
    width: 110px;
    height: 110px;
    border-radius: 50%;
    background: var(--ink);
  }
  .brand__name {
    font-size: 24px;
    font-weight: 700;
    color: var(--ink);
    white-space: nowrap;
  }
  .card--front .divider { top: 92px; height: 210px; }
  .person__name {
    position: absolute;
    left: 356px;
    top: 98px;
    font-size: 25px;
    font-weight: 700;
    color: var(--ink);
  }
  .person__title {
    position: absolute;
    left: 358px;
    top: 129px;
    font-family: "PT Sans Narrow", sans-serif;
    font-size: 20px;
    color: var(--grey);
  }
  .company {
    position: absolute;
    left: 356px;
    top: 176px;
    font-size: 19px;
    color: var(--text);
  }
  .contacts {
    position: absolute;
    left: 356px;
    top: 211px;
    list-style: none;
  }
  .contacts li {
    display: flex;
    align-items: center;
    gap: 12px;
    height: 28px;
    font-size: 18px;
    color: var(--text);
  }
  .contacts svg { width: 16px; height: 18px; flex: none; }
  .bands {
    position: absolute;
    left: 0;
    bottom: 0;
    width: 720px;
    height: 26px;
  }

  /* Back */
  .badge {
    position: absolute;
    left: 191px;
    top: 144px;
    width: 138px;
    height: 138px;
    border-radius: 50%;
    background: var(--badge);
  }
  .card--back .divider { top: 130px; height: 152px; }
  .partner {
    position: absolute;
    left: 352px;
    top: 176px;
    font-size: 56px;
    font-weight: 700;
    line-height: 1;
    letter-spacing: -1px;
    color: var(--partner);
  }
  .web {
    position: absolute;
    left: 0;
    width: 100%;
    top: 347px;
    text-align: center;
    font-size: 19px;
    color: var(--muted);
  }
</style>
</head>
<body>
  <section class="card card--front" aria-label="Business card front">
    <div class="brand">
      <span class="brand__dot"></span>
      <span class="brand__name">Ridge + Studio</span>
    </div>
    <span class="divider"></span>
    <h1 class="person__name">Mark Delford</h1>
    <p class="person__title">architectural designer &amp; Design RDC</p>
    <p class="company">ridge + studio Ltd.</p>
    <ul class="contacts">
      <li>
        <svg viewBox="0 0 16 18" aria-hidden="true"><rect x="3" y="1" width="10" height="16" rx="1.5" fill="none" stroke="#111" stroke-width="2"/><rect x="6" y="13" width="4" height="1.6" fill="#111"/></svg>
        02 5163 2290
      </li>
      <li>
        <svg viewBox="0 0 16 18" aria-hidden="true"><rect x="1" y="5" width="14" height="10" fill="#111"/><path d="M1 5 L8 11 L15 5" fill="none" stroke="#fff" stroke-width="1.2"/></svg>
        mark@rplusd.co.nz
      </li>
      <li>
        <svg viewBox="0 0 16 18" aria-hidden="true"><circle cx="8" cy="9" r="7" fill="#111"/><path d="M4 7 Q7 5 9 8 T12 12" fill="none" stroke="#fff" stroke-width="1.3"/></svg>
        www.rplusd.co.nz
      </li>
    </ul>
    <svg class="bands" viewBox="0 0 720 26" aria-hidden="true">
      <polygon points="0,0 466,0 460,26 0,26" fill="#111111"/>
      <polygon points="475,0 720,0 720,26 466,26" fill="#8c9696"/>
    </svg>
  </section>

  <section class="card card--back" aria-label="Business card back">
    <span class="badge" role="img" aria-label="Partner certification badge"></span>
    <span class="divider"></span>
    <p class="partner">BKTW</p>
    <p class="web">www.rplusd.co.nz</p>
  </section>
</body>
</html>
```